New Business Cards for Tormin Group

We need a new Business Card to compliment our new logo. We are a vibrant design, manufacture and install business providing recreation areas, public parks and Municipal spaces. We want business cards that are classy, modern and clean.

We have recently changed our logo, and are celebrating our 40th anniversary. We want business cards with a new modern design to reflect our status.

Target Market(s)

Customers

Contact Information for Business Card

We need all the details of our 3 offices as per the business card attached. Please disregard the old logo on the business card, the other three files show our new logo.

Requirements
Must have
• All info as per attached business card but with new logo.
Nice to have

```html
<!DOCTYPE html>
<html lang="en">
<head>
<meta charset="utf-8">
<title>Tormin Group – Business Cards</title>
<link href="https://fonts.googleapis.com/css2?family=Open+Sans:wght@400;600;700;800&display=swap" rel="stylesheet">
<style>
  :root {
    --bg: #d6d6d6;
    --charcoal: #4a4b4d;
    --ink: #3e3f41;
    --red: #e2262c;
    --paper: #ffffff;
    --muted: #555658;
  }
  * { box-sizing: border-box; margin: 0; padding: 0; }
  html, body { width: 1200px; height: 900px; overflow: hidden; }
  body {
    background: var(--bg);
    font-family: "Open Sans", Arial, sans-serif;
    position: relative;
  }
  .card {
    position: absolute;
    left: 290px;
    width: 620px;
    height: 354px;
    box-shadow: 0 6px 18px rgba(0,0,0,0.25);
    overflow: hidden;
  }
  .card--front { top: 70px; background: var(--charcoal); }
  .card--back { top: 476px; background: var(--paper); }

  /* front */
  .front-brand {
    position: absolute; inset: 0;
    display: flex; align-items: center; justify-content: center; gap: 18px;
  }
  .brand-dot { width: 64px; height: 64px; border-radius: 50%; background: var(--red); flex: none; }
  .brand-name {
    font-weight: 800; font-size: 44px; letter-spacing: 1px;
    color: var(--paper); text-transform: uppercase; white-space: nowrap;
  }

  /* back */
  .back-brand {
    position: absolute; left: 34px; top: 58px;
    display: flex; flex-direction: column; align-items: flex-end;
  }
  .back-brand-row { display: flex; align-items: center; gap: 10px; }
  .back-brand .brand-dot { width: 46px; height: 46px; }
  .back-brand .brand-name { font-size: 24px; letter-spacing: 0.5px; color: var(--ink); }
  .est { font-size: 12px; color: var(--ink); letter-spacing: 1px; margin-top: 2px; }

  .person { position: absolute; left: 34px; top: 168px; }
  .person-name { font-size: 20px; font-weight: 600; color: var(--red); line-height: 1.2; }
  .person-role { font-size: 14px; color: var(--muted); margin-bottom: 14px; }

  .contact-line {
    display: flex; align-items: center; gap: 7px;
    font-size: 13px; color: var(--ink); line-height: 20px; white-space: nowrap;
  }
  .contact-line svg { width: 13px; height: 13px; flex: none; }

  .offices { position: absolute; left: 352px; top: 22px; }
  .office { margin-bottom: 6px; }
  .office-title { font-size: 13px; font-weight: 700; color: var(--ink); line-height: 18px; }
  .office .contact-line { font-size: 12.5px; line-height: 17px; }

  .footer-band { position: absolute; left: 0; bottom: 0; width: 100%; height: 36px; }
  .footer-band svg { position: absolute; inset: 0; width: 100%; height: 100%; }
  .website {
    position: absolute; left: 40px; bottom: 8px;
    font-size: 14px; color: var(--paper); font-weight: 600;
  }
</style>
</head>
<body>

<section class="card card--front" aria-label="Card front">
  <div class="front-brand">
    <span class="brand-dot"></span>
    <span class="brand-name">Tormin Group</span>
  </div>
</section>

<section class="card card--back" aria-label="Card back">
  <div class="back-brand">
    <div class="back-brand-row">
      <span class="brand-dot"></span>
      <span class="brand-name">Tormin Group</span>
    </div>
    <div class="est">EST. 1979</div>
  </div>

  <div class="person">
    <div class="person-name">Marek Elston</div>
    <div class="person-role">Managing Partner</div>
    <div class="contact-line">
      <svg viewBox="0 0 14 14"><rect x="3.5" y="1" width="7" height="12" rx="1.2" fill="none" stroke="#e2262c" stroke-width="1.3"/><circle cx="7" cy="11" r="0.7" fill="#e2262c"/></svg>
      +971 (0)50 734 8162
    </div>
    <div class="contact-line">
      <svg viewBox="0 0 14 14"><rect x="1" y="3" width="12" height="8.5" fill="none" stroke="#e2262c" stroke-width="1.3"/><path d="M1 3 L7 8 L13 3" fill="none" stroke="#e2262c" stroke-width="1.3"/></svg>
      marek@tormingroup.com
    </div>
  </div>

  <div class="offices">
    <div class="office">
      <div class="office-title">Head Office:</div>
      <div class="contact-line">P.O. Box: 48120 Abu Dhabi, U.A.E.</div>
      <div class="contact-line"><svg viewBox="0 0 14 14"><path d="M3 1.5 L5.5 1.5 L6.5 4.5 L5 5.8 C5.8 7.6 6.6 8.4 8.3 9.1 L9.6 7.6 L12.5 8.6 L12.5 11 C12.5 12 11.6 12.6 10.6 12.5 C5.8 12 2 8.2 1.5 3.4 C1.4 2.4 2 1.5 3 1.5 Z" fill="#e2262c"/></svg>+971 (0)2 5530172</div>
      <div class="contact-line"><svg viewBox="0 0 14 14"><rect x="3.5" y="1" width="7" height="4" fill="#e2262c"/><rect x="1" y="5" width="12" height="6" rx="1" fill="#e2262c"/><rect x="3.5" y="9" width="7" height="4" fill="#fff" stroke="#e2262c" stroke-width="1"/></svg>+971 (0)2 5530173</div>
    </div>
    <div class="office">
      <div class="office-title">Dubai Office:</div>
      <div class="contact-line">P.O. Box: 270845 Dubai, U.A.E.</div>
      <div class="contact-line"><svg viewBox="0 0 14 14"><path d="M3 1.5 L5.5 1.5 L6.5 4.5 L5 5.8 C5.8 7.6 6.6 8.4 8.3 9.1 L9.6 7.6 L12.5 8.6 L12.5 11 C12.5 12 11.6 12.6 10.6 12.5 C5.8 12 2 8.2 1.5 3.4 C1.4 2.4 2 1.5 3 1.5 Z" fill="#e2262c"/></svg>+971 (0)4 3387214</div>
      <div class="contact-line"><svg viewBox="0 0 14 14"><rect x="3.5" y="1" width="7" height="4" fill="#e2262c"/><rect x="1" y="5" width="12" height="6" rx="1" fill="#e2262c"/><rect x="3.5" y="9" width="7" height="4" fill="#fff" stroke="#e2262c" stroke-width="1"/></svg>+971 (0)4 3387215</div>
    </div>
    <div class="office">
      <div class="office-title">Qatar Office:</div>
      <div class="contact-line">P.O. Box: 60392 Doha, Qatar</div>
      <div class="contact-line"><svg viewBox="0 0 14 14"><path d="M3 1.5 L5.5 1.5 L6.5 4.5 L5 5.8 C5.8 7.6 6.6 8.4 8.3 9.1 L9.6 7.6 L12.5 8.6 L12.5 11 C12.5 12 11.6 12.6 10.6 12.5 C5.8 12 2 8.2 1.5 3.4 C1.4 2.4 2 1.5 3 1.5 Z" fill="#e2262c"/></svg>+974 40817356</div>
      <div class="contact-line"><svg viewBox="0 0 14 14"><rect x="3.5" y="1" width="7" height="4" fill="#e2262c"/><rect x="1" y="5" width="12" height="6" rx="1" fill="#e2262c"/><rect x="3.5" y="9" width="7" height="4" fill="#fff" stroke="#e2262c" stroke-width="1"/></svg>+974 40817390</div>
      <div class="contact-line"><svg viewBox="0 0 14 14"><rect x="1" y="3" width="12" height="8.5" fill="none" stroke="#e2262c" stroke-width="1.3"/><path d="M1 3 L7 8 L13 3" fill="none" stroke="#e2262c" stroke-width="1.3"/></svg>sales@tormingroup.com</div>
    </div>
  </div>

  <div class="footer-band">
    <svg viewBox="0 0 620 36" preserveAspectRatio="none">
      <polygon points="0,20 620,20 620,36 0,36" fill="#4a4b4d"/>
      <polygon points="0,0 270,0 300,36 0,36" fill="#e2262c"/>
    </svg>
    <div class="website">www.tormingroup.com</div>
  </div>
</section>

</body>
</html>
```